Natural cosmetics company is looking for a designer to produce the labels of the products and

Hello, Nus need a label and logo design for our brand RM ORGANIC. It is a brand specializing in the sale of 100% Natural cosmetic products on the internet. The first range is based on snail slime. I am looking for a clean design in green tones. The final design must be forwarded to the supplier for printing and shipping of the products. I realized a first idea for a logo, but I am interested in other ideas / suggestions. You have carte blanche :)
Here are the rules to follow for sending labels to the supplier:
• Sizes:
- Airless bottle: 10.3 x 5.5 cm
- Jar: 20x2.5cm
• Files must be in Corel Draw (. cdr) and / or vector PDF format
You must attach the file of the fonts used for the text in the label - We need this file as many fonts are difficult to find and we might need to move some text around for printing purposes
• The logo of your brand must be in a vector format along with all other components.
• Please do not add any borders or any cut marks to the design. We will do it on our end as we need to follow specific indications with our printing suppliers.
• All text and graphics must be at least 6mm from the edge
• The dimensions indicated by us must be respected in the overall size of the label
• The resolution to be used should be 300 cpi and in CMYK
• The text size should be readable and at least 4.5 points.

```html
<!DOCTYPE html>
<html lang="en">
<head>
<meta charset="utf-8">
<title>RM Organic Snail Slime labels</title>
<link rel="stylesheet" href="https://fonts.googleapis.com/css2?family=Questrial&display=swap">
<style>
:root{
  --page:#f4f4f4;
  --label:#ffffff;
  --ink:#111111;
  --band:#000000;
  --gold:#c99a34;
  --yellow:#f4dc72;
  --pale:#fbeeb0;
}
*{box-sizing:border-box;margin:0;padding:0}
html,body{width:1200px;height:923px;overflow:hidden;background:var(--page)}
body{position:relative;font-family:"Questrial",sans-serif;color:var(--ink)}
.label{position:absolute;background:var(--label);overflow:hidden}
.art{position:absolute;background:radial-gradient(ellipse at 50% 50%,var(--pale) 0%,var(--yellow) 45%,var(--gold) 75%,rgba(255,255,255,0) 100%)}
.brand{position:absolute;border-radius:50%;background:var(--label);border:2px solid var(--ink);display:flex;align-items:center;justify-content:center;text-align:center;line-height:1.1}
.col{position:absolute;text-align:center}
.col h3{font-weight:400}
.vertical{position:absolute;transform:rotate(-90deg);transform-origin:left top;white-space:nowrap;line-height:1.15}
.badge{position:absolute}

/* jar strip */
.jar{left:61px;top:74px;width:1067px;height:102px;border-top:3px solid var(--band);border-bottom:3px solid var(--band)}
.jar .art{left:270px;top:-10px;width:345px;height:120px}
.jar .brand{left:364px;top:8px;width:88px;height:88px;font-size:14px}
.jar .product{position:absolute;left:462px;top:44px;font-size:16px}
.jar .volume{position:absolute;left:505px;top:90px;font-size:9px}
.jar .intro{left:5px;top:6px;width:290px;font-size:11.6px;line-height:14px}
.jar .directions{left:620px;top:10px;width:200px;font-size:12.4px;line-height:14.4px}
.jar .ingredients{left:838px;top:10px;width:170px;font-size:12.4px;line-height:14.4px}
.jar .badges{left:1012px;top:6px}
.jar .vertical{left:1035px;top:96px;font-size:8.5px}

/* airless bottle wrap */
.bottle{left:174px;top:404px;width:849px;height:430px}
.bottle .band-top{position:absolute;left:0;top:0;width:100%;height:33px;background:var(--band)}
.bottle .band-bottom{position:absolute;left:0;bottom:0;width:100%;height:33px;background:var(--band);color:#fff;text-align:center;font-size:15px;line-height:33px}
.bottle .art{left:150px;top:33px;width:570px;height:364px}
.bottle .brand{left:352px;top:166px;width:138px;height:138px;font-size:21px}
.bottle .product{position:absolute;left:0;width:100%;top:362px;text-align:center;font-size:25px}
.bottle .intro{left:6px;top:46px;width:164px;font-size:17px;line-height:19.4px}
.bottle .info{left:668px;top:44px;width:150px;font-size:14.5px;line-height:16.8px}
.bottle .info h3{margin-top:10px}
.bottle .info h3:first-child{margin-top:0}
.bottle .badges{left:808px;top:50px}
.bottle .vertical{left:810px;top:392px;font-size:10.5px}
</style>
</head>
<body>

<section class="label jar" aria-label="Jar label">
  <div class="art" role="img" aria-label="Golden yellow brush stroke backdrop"></div>
  <div class="col intro">RM ORGANIC Snail Slime<br>Lorem ipsum dolor sit amet. Dolor dolores kasd sed ipsum elitr amet ut. Et eirmod at stet. Ipsum est gubergren. Quis dolor amet qui sadipscing suscipit dolor. Aliquip wisi vel invidunt accusam augue. Nihil elitr autem. Consectetuer vero elitr. Praesent vero delenit</div>
  <div class="brand">RM<br>Organic</div>
  <div class="product">Snail Slime</div>
  <div class="volume">℮30ml/1.01 fl.oz.</div>
  <div class="col directions"><h3>DIRECTIONS:</h3>Quis dolor amet qui sadipscing suscipit dolor. Aliquip wisi vel invidunt accusam augue. Nihil elitr autem. Consectetuer vero elitr. Praesent vero delenit sed ex</div>
  <div class="col ingredients"><h3>INGREDIENTS:</h3>Water,Butylene Glycol, Tetrapeptide,Palmitoyl Tripeptide,Collagen Amino Acids,Dexpanthenol,Sodium Hyaluronate,Phenoxyethanol</div>
  <svg class="badge badges" width="20" height="88" viewBox="0 0 20 88" aria-hidden="true">
    <rect x="3" y="2" width="14" height="14" fill="var(--ink)"/>
    <circle cx="10" cy="36" r="9" fill="var(--ink)"/>
    <circle cx="10" cy="60" r="9" fill="var(--ink)"/>
    <rect x="3" y="72" width="14" height="14" fill="none" stroke="var(--ink)" stroke-width="1.2"/>
  </svg>
  <div class="vertical">RM Organic,<br>Adress,adress,adress<br>MADE IN CHINA</div>
</section>

<section class="label bottle" aria-label="Airless bottle label">
  <div class="band-top"></div>
  <div class="art" role="img" aria-label="Golden yellow brush stroke backdrop"></div>
  <div class="col intro">RM ORGANIC<br>Snail Slime<br>Lorem ipsum dolor sit amet. Dolor dolores kasd sed ipsum elitr amet ut. Et eirmod at stet. Ipsum est gubergren. Quis dolor amet qui sadipscing suscipit dolor. Aliquip wisi vel invidunt accusam augue. Nihil elitr autem. Consectetuer vero elitr. Praesent vero delenit sed ex</div>
  <div class="brand">RM<br>Organic</div>
  <div class="product">Snail Slime</div>
  <div class="col info">
    <h3>INGREDIENTS:</h3>
    <p>Water,<br>Butylene Glycol,<br>Tetrapeptide,<br>Palmitoyl Tripeptide,<br>Collagen Amino Acids,Dexpanthenol,<br>Sodium Hyaluronate,<br>Phenoxyethanol,<br>Ethylhexylglycerin</p>
    <h3>DIRECTIONS:</h3>
    <p>Quis dolor amet qui sadipscing suscipit dolor. Aliquip wisi vel invidunt accusam augue. Nihil elitr autem. Consectetuer vero elitr. Praesent vero delenit sed ex</p>
  </div>
  <svg class="badge badges" width="36" height="180" viewBox="0 0 36 180" aria-hidden="true">
    <rect x="8" y="2" width="20" height="20" fill="var(--ink)"/>
    <circle cx="18" cy="62" r="16" fill="var(--ink)"/>
    <circle cx="18" cy="112" r="16" fill="var(--ink)"/>
    <rect x="6" y="152" width="24" height="26" fill="none" stroke="var(--ink)" stroke-width="1.5"/>
  </svg>
  <div class="vertical">RM Organic,<br>Adress,adress,adress<br>MADE IN CHINA</div>
  <div class="band-bottom">℮30ml/1.01 fl.oz.</div>
</section>

</body>
</html>
```